Web Design For Marlow Pool Service

We are working with a company that wants a website for their pool service. Some sites to use for content/competitors and inspiration:
https://sacramento.brightwaterpoolco.example/builder/newbuild/repair/ppc
https://hollowbrookpoolcareplus.example/
https://lakemontpoolservice.example/
https://www.dravenspoolresurfacing.example/pool-renovation-ga/
Thank you for taking the time to consider designing a website for us. We are web developers based in Stockton, CA, USA. Most of our projects go through the same process. Understanding this process may help you win a project with us. We custom-code all of our websites in-house. We don’t have any requirements as to what tools you use for your design, but we prefer Figma files. For any design that we label as four-stars, we send it to the client for review. The client picks the final design they want us to use. Once we complete this process, we will continue to show additional clients all the four-star sites and purchase them later. Your designs will have multiple chances to sell. For better chances of success, we ask that you follow these guidelines.
IMAGES:
If you use any images or icons in the design, we ask that you have a link to the asset so we can purchase the image/icon. Most of the designs we submit do not have the customer’s images on them unless they have some great images. Be creative; show us the feeling you are trying to portray with your image choices. Use any royalty-free site you choose. We subscribe to Adobe and mainly use their images, but we can purchase images outside of Adobe. PLEASE NOTE: we will not submit designs to clients with watermarks on the images.
FONTS:
We ask that you identify the fonts used in the design. This can be done in a message if you want. We typically use Google Fonts and Adobe Fonts.
CONTENT:
We're always open to different content and ideas. We often submit designs with stock images so the client can see our vision. We typically take pictures after the website launch to use their images with our vision. Lorem Ipsum is fine for paragraphs, but we ask that you write the headers in correct English. We want to be able to show the vision and identify the sections of the website.
INSPIRATION:
We typically add a couple of links in the brief of websites we like to help you get started in your design.
REVISIONS:
We do not often ask for revisions of the designs unless we see something in the design that may not appeal to the client. If there are slight changes that we want to make, we do that in the development process.
FEEDBACK:
We rarely give feedback on designs during the design process. We are working on many website projects and do not have the time to provide feedback. We usually respond if your request is well thought out and asks specific questions, but a note asking “feedback, please” usually goes unanswered.
Number of Pages Required
1 page
Look and feel
Each slider illustrates characteristics of the customer's brand and the style your logo design should communicate.

```html
<!DOCTYPE html>
<html lang="en">
<head>
<meta charset="utf-8">
<title>Marlow Pool Service</title>
<link href="https://fonts.googleapis.com/css2?family=Alegreya:wght@400;500&family=Inter:ital,wght@0,400;0,500;0,600;1,400&display=swap" rel="stylesheet">
<style>
:root{
  --blue:#2196f3;
  --blue-dark:#1565c0;
  --navy:#0c2550;
  --ink:#1d2433;
  --text:#444b57;
  --sky:#d9eefc;
  --white:#ffffff;
}
*{box-sizing:border-box;margin:0;padding:0}
html,body{width:1200px;height:5286px;overflow:hidden}
body{font-family:"Inter",sans-serif;color:var(--text);background:var(--white);position:relative}
section,header,footer{position:absolute;left:0;width:1200px}
.abs{position:absolute}
.eyebrow{font-family:"Alegreya",serif;font-size:11px;letter-spacing:2px;color:var(--blue);text-transform:uppercase}
.h2{font-family:"Alegreya",serif;font-weight:400;color:var(--ink);font-size:38px;line-height:1.1}
.btn{position:absolute;display:flex;align-items:center;justify-content:center;gap:10px;background:var(--blue);color:#fff;font-size:14px;font-weight:600;border-radius:0 14px 0 14px;box-shadow:0 6px 16px rgba(33,150,243,.35)}
.btn svg{width:14px;height:14px}

/* header */
.site-header{top:0;height:78px;background:#fff;z-index:5}
.brand{position:absolute;left:105px;top:22px;display:flex;align-items:center;gap:10px}
.brand-dot{width:14px;height:14px;border-radius:50%;background:var(--blue)}
.brand-name{font-family:"Alegreya",serif;font-size:22px;color:var(--blue);font-weight:400}
.nav{position:absolute;left:425px;top:29px;display:flex;gap:28px;font-size:14px;color:var(--ink)}
.call{position:absolute;left:860px;top:0;width:237px;height:62px;background:var(--blue);border-radius:0 0 6px 6px;display:flex;align-items:center;gap:14px;padding-left:14px;color:#fff}
.call-icon{width:36px;height:36px;border-radius:50%;background:#fff;display:flex;align-items:center;justify-content:center}
.call small{display:block;font-size:11px;font-weight:600}
.call strong{font-size:16px;font-weight:600}

/* hero */
.hero{top:0;height:720px;overflow:hidden}
.hero-photo{position:absolute;inset:0;background:linear-gradient(180deg,#8a8e86 0%,#a9a896 25%,#5fa4c4 55%,#2b8fd0 80%,#1d78c4 100%)}
.hero-shade{position:absolute;inset:0;background:rgba(10,30,50,.25)}
.hero-eyebrow{position:absolute;top:244px;width:100%;text-align:center;font-family:"Alegreya",serif;color:#fff;letter-spacing:4px;font-size:16px}
.hero-title{position:absolute;top:270px;width:100%;text-align:center;font-family:"Alegreya",serif;font-weight:400;color:#fff;font-size:58px;line-height:1.05}
.hero-sub{position:absolute;top:403px;width:100%;text-align:center;color:#fff;font-size:14px}
.scroll{position:absolute;left:565px;top:560px;width:70px;height:70px;border:1px dashed rgba(255,255,255,.6);border-radius:50%;color:#fff;font-size:9px;letter-spacing:2px;display:flex;align-items:center;justify-content:center;text-align:center}
.hero-wave{position:absolute;left:0;bottom:0;width:1200px;height:150px}

/* about */
.about{top:720px;height:480px}
.about-photo{position:absolute;left:150px;top:35px;width:342px;height:405px;background:linear-gradient(160deg,#5fa9d8,#b88f72 45%,#2f4f80);border-radius:0 30px 0 0}
.about-photo-small{position:absolute;left:376px;top:310px;width:182px;height:215px;border:5px solid #fff;border-radius:0 30px 0 30px;background:linear-gradient(180deg,#7bb24a 0%,#3fa0d8 40%,#1f72b8 100%);box-shadow:0 10px 20px rgba(0,0,0,.15)}
.about-text{position:absolute;left:635px;top:105px;width:360px}
.about-text .h2{margin:10px 0 22px}
.about-text p{font-size:14px;line-height:24px;color:var(--text)}

/* package */
.package{top:1200px;height:800px;overflow:hidden}
.package-photo{position:absolute;inset:0;background:linear-gradient(180deg,#fff 0%,#d8c9b1 18%,#c9a880 40%,#7fc0dc 62%,#4aa6d6 78%,#fff 100%)}
.package-circle{position:absolute;left:160px;top:165px;width:492px;height:492px;border-radius:50%;background:#fff;border:6px solid var(--blue);box-shadow:0 10px 30px rgba(0,0,0,.2);text-align:center}
.package-circle h3{font-family:"Alegreya",serif;font-weight:400;font-size:40px;line-height:40px;color:var(--navy);margin-top:100px}
.package-list{list-style:none;text-align:left;margin:32px 0 0 140px;font-size:12px;font-weight:500;color:var(--blue-dark)}
.package-list li{display:flex;align-items:center;gap:10px;height:33px}
.tick{width:16px;height:16px;flex:none}

/* services */
.services{top:2000px;height:655px;background:linear-gradient(180deg,#fff 0%,#e6f4fd 20%,#cbe7f9 60%,#fff 100%)}
.services .eyebrow{position:absolute;top:40px;width:100%;text-align:center}
.services .h2{position:absolute;top:65px;width:100%;text-align:center}
.svc{position:absolute;top:145px;width:210px;height:390px;background:#fff;border-radius:0 22px 0 0;box-shadow:0 10px 25px rgba(0,50,100,.1);text-align:center}
.svc-photo{height:172px;border-radius:0 22px 0 0}
.svc-icon{position:absolute;left:79px;top:145px;width:52px;height:52px;border-radius:50%;background:var(--blue);border:4px solid #fff;display:flex;align-items:center;justify-content:center}
.svc h3{font-family:"Alegreya",serif;font-weight:500;font-size:20px;line-height:22px;color:var(--ink);margin-top:34px}
.svc em{display:block;font-size:11px;color:var(--blue);margin:6px 0 12px}
.svc p{font-size:12px;line-height:17px;padding:0 22px;color:var(--text)}
.svc-btn{position:absolute;left:40px;bottom:24px;width:130px;height:30px;border:1px solid var(--blue);border-radius:0 10px 0 10px;font-size:11px;font-weight:600;color:var(--blue);display:flex;align-items:center;justify-content:center}

/* why */
.why{top:2655px;height:630px}
.why .eyebrow{position:absolute;left:150px;top:90px}
.why .h2{position:absolute;left:150px;top:115px}
.why-list{position:absolute;left:150px;top:190px;width:440px;list-style:none}
.why-list li{display:flex;gap:14px;font-size:14px;line-height:22px;color:var(--ink);margin-bottom:12px}
.why-list .tick{margin-top:3px}
.why-photo{position:absolute;left:690px;top:0;width:510px;height:430px;border-radius:260px 0 0 0;background:linear-gradient(180deg,#6f6a55 0%,#8c7f66 40%,#3c8ec8 75%,#1d78c4 100%)}
.why-badge{position:absolute;left:778px;top:410px;width:150px;height:150px;border-radius:50%;background:radial-gradient(circle,#3ca4f0,#1a6fc0);border:6px solid #fff;box-shadow:0 8px 20px rgba(0,0,0,.2)}

/* reviews */
.reviews{top:3285px;height:555px;overflow:hidden}
.reviews-bg{position:absolute;inset:0;background:linear-gradient(180deg,#fff 0%,#e3edf4 25%,#bfd6e6 60%,#8fc2e3 85%,#fff 100%)}
.reviews .eyebrow{position:absolute;top:22px;width:100%;text-align:center}
.reviews .h2{position:absolute;top:42px;width:100%;text-align:center}
.review{position:absolute;top:150px;width:287px;height:295px;background:#fff;border-radius:0 26px 0 26px;text-align:center;box-shadow:0 10px 25px rgba(0,40,80,.08)}
.avatar{position:absolute;left:109px;top:-40px;width:68px;height:68px;border-radius:50%;border:4px solid #fff;box-shadow:0 0 0 2px var(--blue)}
.review h4{font-family:"Alegreya",serif;font-weight:400;color:var(--blue);font-size:20px;margin-top:42px}
.review p{font-size:13.5px;line-height:21px;color:var(--ink);padding:0 20px;margin-top:12px}
.stars{display:flex;justify-content:center;gap:3px;margin-top:12px}
.quote-mark{position:absolute;left:118px;bottom:-22px;font-family:"Alegreya",serif;font-size:90px;line-height:70px;color:#b7bec7}

/* areas */
.areas{top:3840px;height:550px;overflow:hidden}
.areas-left{position:absolute;left:0;top:0;width:520px;height:100%;background:linear-gradient(180deg,#2a98f0 0%,#1e6fc7 50%,#163a78 100%)}
.areas-map{position:absolute;left:512px;top:0;width:688px;height:100%;background:linear-gradient(160deg,#203a6a,#13264c 60%,#1c3d72)}
.areas .eyebrow{position:absolute;left:150px;top:92px;color:#fff}
.areas .h2{position:absolute;left:150px;top:115px;color:#fff}
.areas-rule{position:absolute;left:150px;top:163px;width:215px;height:2px;background:#fff}
.areas-list{position:absolute;left:150px;top:185px;list-style:none;color:#fff;font-size:14px}
.areas-list li{display:flex;align-items:center;gap:10px;height:31px}
.btn-white{background:#fff;color:var(--blue);box-shadow:none}

/* estimate */
.estimate{top:4390px;height:580px;overflow:hidden}
.estimate-bg{position:absolute;inset:0;background:linear-gradient(180deg,#fff 0%,#b9d1cf 20%,#8aa7b4 55%,#3f7ca8 85%,#24609a 100%)}
.estimate-frame{position:absolute;left:245px;top:85px;width:710px;height:415px;border:6px solid rgba(255,255,255,.85);border-radius:30px;background:rgba(255,255,255,.12)}
.estimate-card{position:absolute;left:8px;top:8px;right:8px;bottom:8px;background:var(--navy);border-radius:20px}
.estimate h2{position:absolute;top:28px;width:100%;text-align:center;font-family:"Alegreya",serif;font-weight:400;color:#fff;font-size:38px}
.field{position:absolute;height:44px;background:#fff;font-size:12px;color:var(--ink);padding-left:16px;display:flex;align-items:center}
.field svg{position:absolute;right:16px;top:18px}

/* footer */
.site-footer{top:4965px;height:321px;background:linear-gradient(180deg,#1f4f92 0%,#15336a 60%,#0f2a5a 100%);color:#fff}
.foot-brand{position:absolute;left:160px;top:68px;display:flex;align-items:center;gap:10px}
.foot-brand .brand-name{color:#fff;font-size:20px}
.socials{position:absolute;left:175px;top:120px;display:flex;gap:10px}
.socials span{width:24px;height:24px;border-radius:50%;border:1px solid rgba(255,255,255,.6)}
.foot-col{position:absolute;top:68px}
.foot-col h5{font-family:"Alegreya",serif;font-weight:400;font-size:18px;margin-bottom:16px}
.foot-col li{list-style:none;font-size:13px;line-height:30px}
.foot-col.contact li{display:flex;gap:10px;align-items:flex-start;line-height:18px;margin-bottom:12px}
.copyright{position:absolute;top:270px;width:100%;text-align:center;font-size:13px}
</style>
</head>
<body>

<header class="site-header">
  <div class="brand"><span class="brand-dot"></span><span class="brand-name">Marlow Pool Service</span></div>
  <nav class="nav"><span>About Us</span><span>Services</span><span>Why Us</span><span>Contact Us</span></nav>
  <div class="call">
    <span class="call-icon"><svg width="18" height="18" viewBox="0 0 24 24"><path fill="#2196f3" d="M6.6 10.8a15 15 0 0 0 6.6 6.6l2.2-2.2c.3-.3.7-.4 1-.2 1.1.4 2.3.6 3.6.6.6 0 1 .4 1 1V20c0 .6-.4 1-1 1A17 17 0 0 1 3 4c0-.6.4-1 1-1h3.5c.6 0 1 .4 1 1 0 1.3.2 2.5.6 3.6.1.3 0 .7-.2 1z"/></svg></span>
    <span><small>Call Us today</small><strong>+1 (555) 987-2310</strong></span>
  </div>
</header>

<section class="hero">
  <div class="hero-photo" role="img" aria-label="Backyard swimming pool with rock waterfall and palms"></div>
  <div class="hero-shade"></div>
  <div class="hero-eyebrow">MARLOW POOL SERVICE</div>
  <h1 class="hero-title">Your Trusted Pool<br>Maintenance Partner</h1>
  <div class="hero-sub">Excellence in Pool Care and Maintenance Solutions</div>
  <div class="btn" style="left:486px;top:450px;width:228px;height:50px">Request an Estimate</div>
  <div class="scroll">SCROLL<br>DOWN</div>
  <svg class="hero-wave" viewBox="0 0 1200 150" preserveAspectRatio="none">
    <path d="M0 70 C200 140 420 150 620 120 C820 90 1000 60 1200 0 L1200 150 L0 150 Z" fill="#fff"/>
    <path d="M0 60 C200 130 420 140 620 110 C820 80 1000 50 1200 -10" fill="none" stroke="#8fd0f7" stroke-width="6" opacity=".7"/>
  </svg>
</section>

<section class="about">
  <div class="about-photo" role="img" aria-label="Pool technician holding a cleaning hose"></div>
  <div class="about-photo-small" role="img" aria-label="Robotic pool cleaner underwater"></div>
  <div class="about-text">
    <div class="eyebrow">About us</div>
    <h2 class="h2">Your Pool,<br>Our Passion</h2>
    <p>At Marlow Pool Service, we are committed to delivering unparalleled pool maintenance and care services to ensure your pool remains a source of joy and relaxation. With years of expertise and a dedicated team of professionals, we pride ourselves on our commitment to excellence and customer satisfaction.</p>
  </div>
</section>

<section class="package">
  <div class="package-photo" role="img" aria-label="Woman in a sun hat relaxing at the edge of a resort pool"></div>
  <div class="package-circle">
    <h3>Marlow's<br>Seasonal Saver<br>Package</h3>
    <ul class="package-list">
      <li><svg class="tick" viewBox="0 0 16 16"><circle cx="8" cy="8" r="7" fill="none" stroke="#2196f3"/><path d="M5 8.2l2 2 4-4" fill="none" stroke="#2196f3" stroke-width="1.5"/></svg>Opening and Closing Services</li>
      <li><svg class="tick" viewBox="0 0 16 16"><circle cx="8" cy="8" r="7" fill="none" stroke="#2196f3"/><path d="M5 8.2l2 2 4-4" fill="none" stroke="#2196f3" stroke-width="1.5"/></svg>Routine Cleaning</li>
      <li><svg class="tick" viewBox="0 0 16 16"><circle cx="8" cy="8" r="7" fill="none" stroke="#2196f3"/><path d="M5 8.2l2 2 4-4" fill="none" stroke="#2196f3" stroke-width="1.5"/></svg>Equipment Inspections</li>
      <li><svg class="tick" viewBox="0 0 16 16"><circle cx="8" cy="8" r="7" fill="none" stroke="#2196f3"/><path d="M5 8.2l2 2 4-4" fill="none" stroke="#2196f3" stroke-width="1.5"/></svg>Discounted Rates</li>
      <li><svg class="tick" viewBox="0 0 16 16"><circle cx="8" cy="8" r="7" fill="none" stroke="#2196f3"/><path d="M5 8.2l2 2 4-4" fill="none" stroke="#2196f3" stroke-width="1.5"/></svg>Professional Expertise</li>
    </ul>
  </div>
  <div class="btn" style="left:290px;top:615px;width:230px;height:54px">Request an Estimate</div>
</section>

<section class="services">
  <div class="eyebrow">Our services</div>
  <h2 class="h2">What We Do</h2>
  <article class="svc" style="left:150px">
    <div class="svc-photo" role="img" aria-label="Technician testing pool water" style="background:linear-gradient(180deg,#3d5f8c,#2d7fc0)"></div>
    <div class="svc-icon"><svg width="22" height="22" viewBox="0 0 24 24" fill="none" stroke="#fff" stroke-width="1.6"><rect x="5" y="4" width="14" height="16" rx="2"/><path d="M9 9h6M9 13h6"/></svg></div>
    <h3>Regular<br>Maintenance</h3><em>Keeping Your Pool Crystal Clear</em>
    <p>Our regular maintenance services include routine cleaning</p>
    <div class="svc-btn">Request a Service</div>
  </article>
  <article class="svc" style="left:380px">
    <div class="svc-photo" role="img" aria-label="Worker brushing a pool" style="background:linear-gradient(180deg,#6c8c6a,#2ea0d8)"></div>
    <div class="svc-icon"><svg width="22" height="22" viewBox="0 0 24 24" fill="none" stroke="#fff" stroke-width="1.6"><rect x="4" y="6" width="16" height="13" rx="2"/><path d="M9 6V4h6v2M12 10v5M9.5 12.5h5"/></svg></div>
    <h3>Repairs &amp;<br>Troubleshooting</h3><em>Swift Solutions for Pool Problems</em>
    <p>Our skilled technicians are equipped to handle all your pool repair needs</p>
    <div class="svc-btn">Request a Service</div>
  </article>
  <article class="svc" style="left:610px">
    <div class="svc-photo" role="img" aria-label="Installer fitting pool equipment" style="background:linear-gradient(180deg,#2f8fd2,#a33a3a 70%,#2d7fc0)"></div>
    <div class="svc-icon"><svg width="22" height="22" viewBox="0 0 24 24" fill="none" stroke="#fff" stroke-width="1.6"><circle cx="12" cy="12" r="3"/><path d="M12 3v3M12 18v3M3 12h3M18 12h3M5.6 5.6l2.1 2.1M16.3 16.3l2.1 2.1M5.6 18.4l2.1-2.1M16.3 7.7l2.1-2.1"/></svg></div>
    <h3>Equipment<br>Installation</h3><em>Upgrade Your Pool Experience</em>
    <p>We'll help you choose and install the perfect equipment for your pool</p>
    <div class="svc-btn">Request a Service</div>
  </article>
  <article class="svc" style="left:840px">
    <div class="svc-photo" role="img" aria-label="Pool cover being removed" style="background:linear-gradient(180deg,#9fc8e8,#4d94cf)"></div>
    <div class="svc-icon"><svg width="22" height="22" viewBox="0 0 24 24" fill="none" stroke="#fff" stroke-width="1.6"><rect x="4" y="5" width="16" height="15" rx="2"/><path d="M4 10h16M8 3v4M16 3v4"/></svg></div>
    <h3>Seasonal Opening<br>&amp; Closing</h3><em>Year-Round Pool Care</em>
    <p>Trust us to handle all the details of seasonal pool opening and closing</p>
    <div class="svc-btn">Request a Service</div>
  </article>
</section>

<section class="why">
  <div class="eyebrow">Why us</div>
  <h2 class="h2">Why Choose Us</h2>
  <ul class="why-list">
    <li><svg class="tick" viewBox="0 0 16 16"><circle cx="8" cy="8" r="8" fill="#2196f3"/><path d="M4.5 8.2l2.3 2.3 4.5-4.5" fill="none" stroke="#fff" stroke-width="1.6"/></svg>Our team consists of experienced professionals with in-depth knowledge of pool care and maintenance.</li>
    <li><svg class="tick" viewBox="0 0 16 16"><circle cx="8" cy="8" r="8" fill="#2196f3"/><path d="M4.5 8.2l2.3 2.3 4.5-4.5" fill="none" stroke="#fff" stroke-width="1.6"/></svg>We pride ourselves on our punctuality, reliability, and dedication to customer satisfaction.</li>
    <li><svg class="tick" viewBox="0 0 16 16"><circle cx="8" cy="8" r="8" fill="#2196f3"/><path d="M4.5 8.2l2.3 2.3 4.5-4.5" fill="none" stroke="#fff" stroke-width="1.6"/></svg>We understand that every pool is unique, which is why we offer tailored solutions to meet your specific needs.</li>
    <li><svg class="tick" viewBox="0 0 16 16"><circle cx="8" cy="8" r="8" fill="#2196f3"/><path d="M4.5 8.2l2.3 2.3 4.5-4.5" fill="none" stroke="#fff" stroke-width="1.6"/></svg>Enjoy high-quality services at competitive prices, with no compromise on excellence.</li>
  </ul>
  <div class="btn" style="left:150px;top:455px;width:230px;height:54px">Request an Estimate</div>
  <svg class="abs" style="left:640px;top:0" width="560" height="600" viewBox="0 0 560 600">
    <path d="M60 0 C10 150 40 380 230 470 C360 530 470 500 560 450" fill="none" stroke="#2196f3" stroke-width="14"/>
  </svg>
  <div class="why-photo" role="img" aria-label="Pool technician in blue overalls cleaning a pool with a brush"></div>
  <div class="why-badge"></div>
</section>

<section class="reviews">
  <div class="reviews-bg" role="img" aria-label="Blurred pool ladder and water"></div>
  <div class="eyebrow">Testimonials</div>
  <h2 class="h2">Our Reviews</h2>
  <svg width="0" height="0" style="position:absolute"><defs><path id="star" d="M9 0l2.6 5.6 6 .7-4.5 4.1 1.2 6L9 13.4 3.7 16.4l1.2-6L.4 6.3l6-.7z"/></defs></svg>
  <article class="review" style="left:150px">
    <div class="avatar" role="img" aria-label="Portrait of Emily S." style="background:#d9a57a"></div>
    <h4>Emily S.</h4>
    <p>"Marlow Pool Service is simply fantastic! Their attention to detail and professionalism are unmatched. My pool has never looked better!"</p>
    <div class="stars"><svg width="110" height="18" viewBox="0 0 110 18"><g fill="#f7d21b"><use href="#star"/><use href="#star" x="23"/><use href="#star" x="46"/><use href="#star" x="69"/><use href="#star" x="92"/></g></svg></div>
    <div class="quote-mark">”</div>
  </article>
  <article class="review" style="left:456px">
    <div class="avatar" role="img" aria-label="Portrait of Michael R" style="background:#7a5a45"></div>
    <h4>Michael R</h4>
    <p>"Five stars for Marlow Pool Service! Their Seasonal Saver Package saved me time and money. Highly recommend their expert team."</p>
    <div class="stars"><svg width="110" height="18" viewBox="0 0 110 18"><g fill="#f7d21b"><use href="#star"/><use href="#star" x="23"/><use href="#star" x="46"/><use href="#star" x="69"/><use href="#star" x="92"/></g></svg></div>
    <div class="quote-mark">”</div>
  </article>
  <article class="review" style="left:763px">
    <div class="avatar" role="img" aria-label="Portrait of Jessica W." style="background:#d84a4a"></div>
    <h4>Jessica W.</h4>
    <p>"Impressed with Marlow's service! From opening to closing, they handled everything seamlessly. My pool is now the highlight of my backyard!"</p>
    <div class="stars"><svg width="110" height="18" viewBox="0 0 110 18"><g fill="#f7d21b"><use href="#star"/><use href="#star" x="23"/><use href="#star" x="46"/><use href="#star" x="69"/><use href="#star" x="92"/></g></svg></div>
    <div class="quote-mark">”</div>
  </article>
</section>

<section class="areas">
  <div class="areas-left"></div>
  <div class="areas-map" role="img" aria-label="Street map of the service area with location pins"></div>
  <div class="eyebrow">Service areas</div>
  <h2 class="h2">Areas We Serve</h2>
  <div class="areas-rule"></div>
  <ul class="areas-list">
    <li><svg width="12" height="16" viewBox="0 0 12 16"><path d="M6 0a6 6 0 0 1 6 6c0 4.5-6 10-6 10S0 10.5 0 6a6 6 0 0 1 6-6z" fill="#7cc4ff"/><circle cx="6" cy="6" r="2.2" fill="#1e6fc7"/></svg>Seaside City, CA</li>
    <li><svg width="12" height="16" viewBox="0 0 12 16"><path d="M6 0a6 6 0 0 1 6 6c0 4.5-6 10-6 10S0 10.5 0 6a6 6 0 0 1 6-6z" fill="#7cc4ff"/><circle cx="6" cy="6" r="2.2" fill="#1e6fc7"/></svg>Sunnyvale, FL</li>
    <li><svg width="12" height="16" viewBox="0 0 12 16"><path d="M6 0a6 6 0 0 1 6 6c0 4.5-6 10-6 10S0 10.5 0 6a6 6 0 0 1 6-6z" fill="#7cc4ff"/><circle cx="6" cy="6" r="2.2" fill="#1e6fc7"/></svg>Oceanview Heights, TX</li>
    <li><svg width="12" height="16" viewBox="0 0 12 16"><path d="M6 0a6 6 0 0 1 6 6c0 4.5-6 10-6 10S0 10.5 0 6a6 6 0 0 1 6-6z" fill="#7cc4ff"/><circle cx="6" cy="6" r="2.2" fill="#1e6fc7"/></svg>Coastal Haven, NC</li>
    <li><svg width="12" height="16" viewBox="0 0 12 16"><path d="M6 0a6 6 0 0 1 6 6c0 4.5-6 10-6 10S0 10.5 0 6a6 6 0 0 1 6-6z" fill="#7cc4ff"/><circle cx="6" cy="6" r="2.2" fill="#1e6fc7"/></svg>Harbor Springs, MI</li>
    <li><svg width="12" height="16" viewBox="0 0 12 16"><path d="M6 0a6 6 0 0 1 6 6c0 4.5-6 10-6 10S0 10.5 0 6a6 6 0 0 1 6-6z" fill="#7cc4ff"/><circle cx="6" cy="6" r="2.2" fill="#1e6fc7"/></svg>Bayfront Bay, WA</li>
  </ul>
  <div class="btn btn-white" style="left:150px;top:410px;width:230px;height:54px">Request an Estimate</div>
</section>

<section class="estimate">
  <div class="estimate-bg" role="img" aria-label="Backyard pool with wooden pergola and trees"></div>
  <div class="estimate-frame">
    <div class="estimate-card">
      <h2>Request an Estimate</h2>
      <div class="field" style="left:30px;top:86px;width:300px">First  Name *</div>
      <div class="field" style="left:347px;top:86px;width:303px">Last Name *</div>
      <div class="field" style="left:30px;top:146px;width:200px">Email Address *</div>
      <div class="field" style="left:240px;top:146px;width:200px">Phone *</div>
      <div class="field" style="left:450px;top:146px;width:200px">Choose your city<svg width="10" height="6" viewBox="0 0 10 6"><path d="M0 0h10L5 6z" fill="#1d2433"/></svg></div>
      <div class="field" style="left:30px;top:206px;width:620px">Message</div>
      <div class="btn" style="left:30px;top:268px;width:195px;height:46px;box-shadow:none"><svg viewBox="0 0 16 16"><path d="M1 7.5L15 1 10 15 7.5 9z" fill="#fff"/></svg>Submit Request</div>
    </div>
  </div>
</section>

<footer class="site-footer">
  <div class="foot-brand"><span class="brand-dot" style="background:#fff"></span><span class="brand-name">Marlow Pool Service</span></div>
  <div class="socials"><span></span><span></span><span></span></div>
  <div class="foot-col" style="left:405px"><h5>Quick Links</h5><ul><li>– About Us</li><li>– Services</li><li>– Why Us</li><li>– Contact Us</li></ul></div>
  <div class="foot-col" style="left:565px"><h5>Services</h5><ul><li>Regular Maintenance</li><li>Repairs &amp; Troubleshooting</li><li>Equipment Installation</li><li>Seasonal Opening &amp; Closing</li></ul></div>
  <div class="foot-col contact" style="left:815px"><h5>Contact Us</h5><ul>
    <li><svg width="12" height="16" viewBox="0 0 12 16"><path d="M6 0a6 6 0 0 1 6 6c0 4.5-6 10-6 10S0 10.5 0 6a6 6 0 0 1 6-6z" fill="#4fb0ff"/></svg><span>48 Harborlight Lane<br>Seaside City, CA 98765</span></li>
    <li><svg width="14" height="12" viewBox="0 0 14 12"><rect width="14" height="12" rx="2" fill="#4fb0ff"/><path d="M1 2l6 4 6-4" fill="none" stroke="#15336a"/></svg><span>info@marlowpoolservice.com</span></li>
    <li><svg width="14" height="14" viewBox="0 0 24 24"><path fill="#4fb0ff" d="M6.6 10.8a15 15 0 0 0 6.6 6.6l2.2-2.2c.3-.3.7-.4 1-.2 1.1.4 2.3.6 3.6.6.6 0 1 .4 1 1V20c0 .6-.4 1-1 1A17 17 0 0 1 3 4c0-.6.4-1 1-1h3.5c.6 0 1 .4 1 1 0 1.3.2 2.5.6 3.6.1.3 0 .7-.2 1z"/></svg><span>+1 (555) 987-2310</span></li>
  </ul></div>
  <div class="copyright">Marlow Pool Service - © 2024. All Rights Reserved.</div>
</footer>

</body>
</html>
```